K & R Acre Works. Business card design

We need a business card designed for a new business. We have a bulldozer and tractor service. We clear land and make wildlife food plots. We provide disking, bush hogging, and site prep services.
I have attached an image of a business card that I like and would like my business cards to look similar.

Target Market(s)

anyone needing bulldozer and/or tractor services

Industry/Entity Type

Business

Contact Information for Business Card

K & R Acre Works, Operated by 7-T-Ranch
Wade Colton
601-472-3358
wcr4817@fieldmail-example.com

Font styles to use
Sans Serif

Colors

Designer to choose colors to be used in the design.

Requirements
Must have
• image of tractor and bulldozer
• Land Clearing
• Wildlife food plots
• Bush Hogging
• Disking
• Site prep
Nice to have
• i have included a image of a business card that i like. I would like mine to be similar.

```html
<!DOCTYPE html>
<html lang="en">
<head>
<meta charset="utf-8">
<title>K &amp; R Acre Works – Business Card</title>
<link rel="stylesheet" href="https://fonts.googleapis.com/css2?family=Roboto+Condensed:wght@700&family=Roboto:wght@400;500&display=swap">
<style>
  :root {
    --page-bg: #2a2a2a;
    --card-bg: #f4f4f2;
    --brown: #7a3d0c;
    --brown-dark: #5e2e0a;
    --olive: #9a9630;
    --ink: #2b2b2b;
    --text-grey: #454545;
    --photo-green: #6b7f4a;
    --photo-yellow: #b7a93e;
    --photo-earth: #6a5c48;
  }
  * { margin: 0; padding: 0; box-sizing: border-box; }
  html, body {
    width: 1200px; height: 771px; overflow: hidden;
    background: var(--page-bg);
  }
  .card {
    position: absolute; left: 300px; top: 214px;
    width: 600px; height: 343px;
    border-radius: 18px; overflow: hidden;
    background: var(--card-bg);
    font-family: "Roboto", Arial, sans-serif;
  }
  .edge-strip { position: absolute; left: 0; top: 0; width: 18px; height: 343px; }
  .work-photo {
    position: absolute; right: 0; top: 0; width: 440px; height: 343px;
    background: linear-gradient(170deg, var(--photo-green) 0%, var(--photo-yellow) 45%, var(--photo-earth) 100%);
    -webkit-mask-image: linear-gradient(90deg, transparent 0%, rgba(0,0,0,0.55) 25%, #000 45%);
    mask-image: linear-gradient(90deg, transparent 0%, rgba(0,0,0,0.55) 25%, #000 45%);
  }
  .content { position: absolute; left: 45px; top: 0; }
  .brand {
    position: absolute; top: 50px; white-space: nowrap;
    font-family: "Roboto Condensed", Arial, sans-serif; font-weight: 700;
    font-size: 25px; letter-spacing: 0.5px; color: var(--brown);
  }
  .tagline {
    position: absolute; top: 76px; white-space: nowrap;
    font-family: "Roboto Condensed", Arial, sans-serif; font-weight: 700;
    font-size: 12.5px; letter-spacing: 0.3px; color: var(--ink);
  }
  .person-name {
    position: absolute; top: 103px; white-space: nowrap;
    font-family: "Roboto Condensed", Arial, sans-serif; font-weight: 700;
    font-size: 21px; color: var(--olive);
  }
  .person-role {
    position: absolute; top: 127px; white-space: nowrap;
    font-size: 15px; font-weight: 500; color: var(--brown-dark);
  }
  .operator { font-size: 11px; font-weight: 400; color: var(--text-grey); margin-left: 6px; }
  .contact-list { position: absolute; top: 156px; list-style: none; }
  .contact-list li {
    display: flex; align-items: center; gap: 6px; height: 18px;
    font-size: 14.5px; color: var(--text-grey); white-space: nowrap;
  }
  .contact-list svg { width: 13px; height: 13px; fill: var(--olive); }
  .services-title {
    position: absolute; top: 220px; white-space: nowrap;
    font-family: "Roboto Condensed", Arial, sans-serif; font-weight: 700;
    font-size: 18px; color: var(--olive);
  }
  .service-list { position: absolute; top: 241px; list-style: none; }
  .service-list li {
    height: 18px; font-size: 14.5px; color: var(--text-grey); white-space: nowrap;
  }
  .dot { color: var(--olive); margin-right: 6px; font-size: 13px; }
  .dot.inline { margin: 0 3px; }
</style>
</head>
<body>
  <div class="card">
    <div class="work-photo" role="img" aria-label="Photo of a yellow bulldozer pushing a mound of cleared earth with a small orange tractor beside it"></div>

    <svg class="edge-strip" viewBox="0 0 18 343" aria-hidden="true">
      <polygon points="0,0 18,0 18,104 0,114" fill="var(--brown)"/>
      <polygon points="0,118 18,108 18,343 0,343" fill="var(--olive)"/>
    </svg>

    <div class="content">
      <div class="brand">K &amp; R ACRE WORKS</div>
      <div class="tagline">FOR ALL OF YOUR LAND IMPROVEMENT NEEDS</div>
      <div class="person-name">WADE COLTON</div>
      <div class="person-role">OWNER<span class="operator">Operated by 7-T-Ranch</span></div>

      <ul class="contact-list">
        <li>
          <svg viewBox="0 0 24 24"><path d="M6.6 10.8a15.1 15.1 0 0 0 6.6 6.6l2.2-2.2c.3-.3.7-.4 1-.2 1.1.4 2.3.6 3.6.6.6 0 1 .4 1 1V20c0 .6-.4 1-1 1A17 17 0 0 1 3 4c0-.6.4-1 1-1h3.5c.6 0 1 .4 1 1 0 1.3.2 2.5.6 3.6.1.3 0 .7-.2 1z"/></svg>
          601-472-3358
        </li>
        <li>
          <svg viewBox="0 0 24 24"><path d="M2 5h20v14H2z"/><path d="M2 5l10 8 10-8" fill="none" stroke="#f4f4f2" stroke-width="2"/></svg>
          wcr4817@fieldmail-example.com
        </li>
        <li>
          <svg viewBox="0 0 24 24"><circle cx="12" cy="12" r="10"/><path d="M2 12h20M12 2c3 3 3 17 0 20M12 2c-3 3-3 17 0 20" fill="none" stroke="#f4f4f2" stroke-width="1.5"/></svg>
          kracreworks-example.com
        </li>
      </ul>

      <div class="services-title">WE PROVIDE</div>
      <ul class="service-list">
        <li><span class="dot">&bull;</span>Land Clearing</li>
        <li><span class="dot">&bull;</span>Wildlife food plots</li>
        <li><span class="dot">&bull;</span>Bush Hogging</li>
        <li><span class="dot">&bull;</span>Disking<span class="dot inline">&bull;</span>Site prep</li>
      </ul>
    </div>
  </div>
</body>
</html>
```